Coffee Bag Design for Tollbury Coffee

We’re excited to invite you to help us bring Tollbury Coffee to life on grocery store shelves with a design that embodies our mission of spreading goodness and creating a lasting impact. Tollbury Coffee represents warmth, positivity, and the power of small actions to create ripples of goodness. Each cup not only offers a rich, gourmet coffee experience but also gives back to the community, with $2 from each bag supporting local food banks.

To reflect this vision, we’d love for the design to feature a dark (greyish) blue as the base color to convey depth and quality, complemented by a vibrant light blue that will catch the eye and add energy. Tan or gold accents could add an elegant touch and a feeling of warmth. We are aiming for a look that feels uplifting and engaging, with simplicity and elegance, yet stands out amid other brands on the shelf.

I am attaching the dimension of the bag.

Other information that needs to be listed:
Ingredients: 100% Arabica Coffee
Net Wt. 12 oz. (340 g)
Roasted and distributed by:
Name
Address
email

Text on the back of the bag:
Tollbury Coffee is crafted with a belief that kindness and positivity can spread, touching countless lives with every sip. This gourmet blend delivers a rich taste experience while giving back, as $2 from each bag sold is donated to local food banks to help those in need. Enjoy the warmth and goodness in each cup, knowing you’re making a difference with every purchase.

Thank you!

```html
<!DOCTYPE html>
<html lang="en">
<head>
<meta charset="UTF-8">
<title>Tollbury Coffee – Bag Back, V1</title>
<link rel="stylesheet" href="https://fonts.googleapis.com/css2?family=Montserrat:wght@400;500&family=Playfair+Display:wght@700&display=swap">
<style>
  :root {
    --stage: #172027;
    --bag-navy: #273845;
    --band-blue: #2e4d62;
    --band-olive: #48544f;
    --gold: #c9a77a;
    --sky: #4fb3e0;
    --art-light: #dbe6ef;
    --art-mid: #a9bfd4;
    --art-deep: #7f9bb6;
    --white: #ffffff;
  }
  html, body {
    margin: 0;
    padding: 0;
    width: 1200px;
    height: 1200px;
    overflow: hidden;
    background: var(--stage);
  }
  .canvas {
    position: relative;
    width: 1200px;
    height: 1200px;
    background: var(--stage);
  }
  .bag-back {
    position: absolute;
    left: 224px;
    top: 149px;
    width: 752px;
    height: 902px;
    background: var(--bag-navy);
    overflow: hidden;
  }
  .wave-bands {
    position: absolute;
    inset: 0;
  }
  .gold-frame {
    position: absolute;
    left: 23px;
    top: 27px;
    width: 706px;
    height: 848px;
    border: 1.5px solid var(--gold);
    border-radius: 28px;
    box-sizing: border-box;
  }
  .hero-art {
    position: absolute;
    left: 103px;
    top: 198px;
    width: 546px;
    height: 227px;
    border-radius: 14px;
    background:
      radial-gradient(ellipse at 50% 55%, var(--art-light) 0%, transparent 55%),
      linear-gradient(90deg, var(--art-mid), var(--art-light) 50%, var(--art-mid));
  }
  .story-title {
    position: absolute;
    left: 105px;
    top: 451px;
    margin: 0;
    font-family: 'Playfair Display', serif;
    font-weight: 700;
    font-size: 50px;
    line-height: 1;
    color: var(--gold);
  }
  .story-text {
    position: absolute;
    left: 104px;
    top: 515px;
    width: 548px;
    margin: 0;
    font-family: 'Montserrat', sans-serif;
    font-weight: 400;
    font-size: 20.3px;
    line-height: 25.5px;
    color: var(--sky);
  }
  .roaster {
    position: absolute;
    left: 102px;
    top: 757px;
    font-family: 'Montserrat', sans-serif;
  }
  .roaster-label {
    margin: 0 0 7px;
    font-size: 13.5px;
    letter-spacing: 1.6px;
    color: var(--gold);
  }
  .roaster-details {
    margin: 0;
    font-style: normal;
    font-size: 13.5px;
    line-height: 17px;
    letter-spacing: 1.6px;
    color: var(--sky);
    padding-left: 1px;
  }
  .version-label {
    position: absolute;
    left: 0;
    width: 1200px;
    top: 1084px;
    text-align: center;
    font-family: 'Montserrat', sans-serif;
    font-weight: 400;
    font-size: 62px;
    line-height: 1;
    color: var(--white);
  }
</style>
</head>
<body>
<main class="canvas">
  <section class="bag-back">
    <svg class="wave-bands" width="752" height="902" viewBox="0 0 752 902" aria-hidden="true">
      <path d="M261 0 L360 0 Q500 110 600 260 Q680 350 752 391 L752 475 Q640 420 560 300 Q440 120 261 0 Z" fill="var(--band-blue)"/>
      <path d="M404 0 L484 0 Q580 110 650 200 Q700 230 752 248 L752 379 Q680 350 620 270 Q520 120 404 0 Z" fill="var(--band-olive)"/>
      <path d="M528 0 L602 0 Q660 90 700 140 Q725 160 752 170 L752 232 Q700 210 660 150 Q600 60 528 0 Z" fill="var(--band-blue)"/>
      <path d="M633 0 L702 0 Q730 50 752 80 L752 161 Q710 130 680 70 Q660 30 633 0 Z" fill="var(--band-olive)"/>
      <path d="M732 0 L752 0 L752 30 Q740 15 732 0 Z" fill="var(--band-blue)"/>
    </svg>

    <div class="gold-frame"></div>

    <div class="hero-art" role="img" aria-label="Illustration: two hands holding a cup of latte with rising heart-shaped steam, surrounded by swirling leaves and coffee beans in pale blue tones"></div>

    <h2 class="story-title">Brand Story</h2>

    <p class="story-text">"Tollbury Coffee is crafted with a belief that kindness and positivity can spread, touching countless lives with every sip. This gourmet blend delivers a rich taste experience while giving back, as $2 from each bag sold is donated to local food banks to help those in need. Enjoy the warmth and goodness in each cup, knowing you’re making a difference with every purchase."</p>

    <div class="roaster">
      <p class="roaster-label">Roasted and distributed by</p>
      <address class="roaster-details">
        Your name<br>
        Some Address Here<br>
        youremail@tollmail.com
      </address>
    </div>
  </section>

  <div class="version-label">V1</div>
</main>
</body>
</html>
```